Rebrand & reskin fitbrisko.com (Uncoded)

Fitbrisko.com is a commerce website and app for sports and fitness classes and events. In order to improve its appeal, we invite designers to provide their 'skins' for the landing page, club page and event page. Designers can propose using alternate controls and layouts for these pages, and comment on ways to improve the site's usability. It must remain easy to use on a portrait mobile phone screen, responsive design where necessary to also provide a good experience on desktop.

Please navigate to fitbrisko.com and explore the site, and we look forwards to your suggestions!

Target Market(s)

Primary: Tech-savvy mobile users. Secondary: Desktop users

Industry/Entity Type

Health And Wellness

Number of Pages Required

3 page

Font styles to use
Sans Serif

Colors
ffffff
f37122

Requirements
Must have
• This brief is all about changing the look and feel of the site; the winning design will have an immediate 'wow' factor, yet not sacrifice the ease of finding and paying for classes. It must retain the logo, white and orange must be the primary colours used.
Should not have
• The colour palette must remain roughly as is; for example, a very dark site will not appeal.

```html
<!DOCTYPE html>
<html lang="en">
<head>
<meta charset="utf-8">
<title>Fitbrisko – Events</title>
<link href="https://fonts.googleapis.com/css2?family=Roboto:wght@400;500&family=Open+Sans:wght@400&display=swap" rel="stylesheet">
<style>
:root{
  --orange:#f37122;
  --orange-dark:#c9581a;
  --white:#ffffff;
  --page:#e6e6e6;
  --header:#f4f4f4;
  --sidebar:#3d3d45;
  --nav-text:#3a3a3a;
  --nav-line:#d6d6d6;
  --tab-dark:#2b2b2f;
  --footer:#2a2a2a;
  --footer-text:#9a9a9a;
  --muted:#8a8a8a;
  --shade:rgba(0,0,0,0.4);
}
*{margin:0;padding:0;box-sizing:border-box}
html,body{width:1200px;height:928px;overflow:hidden}
body{position:relative;background:var(--page);font-family:"Open Sans",sans-serif}
.site-header{position:absolute;left:0;top:0;width:1200px;height:102px;background:var(--header);border-bottom:1px solid var(--nav-line)}
.brand{position:absolute;left:117px;top:34px;display:flex;align-items:center;gap:10px}
.brand-dot{width:34px;height:34px;border-radius:50%;background:var(--orange)}
.brand-name{font-family:"Roboto",sans-serif;font-weight:500;font-size:28px;letter-spacing:1px;color:var(--orange)}
.main-nav{position:absolute;left:440px;top:0;height:102px;display:flex;font-family:"Roboto",sans-serif;font-size:17px;color:var(--nav-text)}
.main-nav a{display:flex;align-items:center;justify-content:center;height:102px;text-decoration:none;color:inherit;border-left:1px solid var(--nav-line)}
.main-nav a:first-child{border-left:none}
.main-nav a.active{background:linear-gradient(#3a3a3a,#1a1a1a);color:var(--white)}
.sidebar{position:absolute;left:105px;top:102px;width:223px;height:767px;background:var(--sidebar)}
.side-item{height:57px;display:flex;align-items:center;padding-left:68px;font-family:"Roboto",sans-serif;font-size:17px;color:var(--white);border-bottom:1px solid #55555e;position:relative}
.side-item svg{position:absolute;left:28px;top:50%;transform:translateY(-50%)}
.side-item:last-child{border-bottom:none}
.page-title{position:absolute;left:366px;top:144px;font-family:"Roboto",sans-serif;font-weight:400;font-size:31px;color:#222;letter-spacing:1px}
.event-tabs{position:absolute;left:364px;top:206px;width:210px}
.event-tabs div{height:42px;background:var(--tab-dark);border-bottom:1px solid #444}
.event-tabs div.current{background:var(--orange)}
.event-card{position:absolute;left:574px;top:205px;width:516px;height:371px;background:var(--white);border:1px solid #cfcfcf}
.event-photo{position:absolute;left:908px;top:238px;width:158px;height:158px;border-radius:50%;background:radial-gradient(circle at 50% 40%,#c9a38a,#6f8a5a 70%,#3f5a3a)}
.event-text{position:absolute;left:604px;top:454px;font-size:13px;line-height:22px;color:var(--muted)}
.shade{position:absolute;left:0;top:0;width:1200px;height:869px;background:var(--shade)}
.site-footer{position:absolute;left:0;top:869px;width:1200px;height:59px;background:var(--footer);color:var(--footer-text);font-size:14px;text-align:center;line-height:59px}
.promo{position:absolute;left:376px;top:213px;width:536px;height:252px;background:var(--orange);padding:13px}
.promo-inner{width:100%;height:100%;border:2px solid var(--white);text-align:center;color:var(--white);padding-top:34px}
.promo-title{font-family:"Roboto",sans-serif;font-weight:400;font-size:25px;line-height:34px}
.promo-text{font-size:14.5px;line-height:22px;margin-top:10px}
.promo-button{display:inline-block;margin-top:14px;width:128px;height:40px;border:2px solid var(--white);font-family:"Roboto",sans-serif;font-weight:500;font-size:16px;line-height:36px;color:var(--white);text-decoration:none}
</style>
</head>
<body>
<header class="site-header">
  <div class="brand"><span class="brand-dot"></span><span class="brand-name">FITBRISKO</span></div>
  <nav class="main-nav">
    <a href="#" style="width:135px">CALENDAR</a>
    <a href="#" style="width:110px">FEED</a>
    <a href="#" style="width:142px">NEAR BY</a>
    <a href="#" style="width:139px">CLASSES</a>
    <a href="#" class="active" style="width:115px">EVENT</a>
  </nav>
</header>

<aside class="sidebar">
  <div class="side-item" style="height:70px">
    <svg width="26" height="22" viewBox="0 0 26 22"><path d="M2 8h9V3l8 8-8 8v-5H2z" fill="#fff"/><path d="M15 2h8v18h-8" fill="none" stroke="#fff" stroke-width="2.5"/></svg>LOGIN</div>
  <div class="side-item" style="height:55px">
    <svg width="24" height="28" viewBox="0 0 24 28"><rect x="2" y="2" width="20" height="24" rx="2" fill="none" stroke="#fff" stroke-width="2"/><rect x="12" y="2" width="4" height="8" fill="#fff"/><path d="M12 15l1.5 3 3 .4-2.2 2 .6 3-2.9-1.5-2.9 1.5.6-3-2.2-2 3-.4z" fill="#fff"/></svg>MY DIARY</div>
  <div class="side-item" style="height:56px">
    <svg width="34" height="34" viewBox="0 0 34 34"><path d="M17 1l16 16-16 16L1 17z" fill="#fff"/><rect x="8" y="14" width="18" height="6" fill="#3d3d45"/><rect x="6" y="12" width="4" height="10" fill="#3d3d45"/><rect x="24" y="12" width="4" height="10" fill="#3d3d45"/></svg>MY CLUBS</div>
  <div class="side-item" style="height:58px">
    <svg width="26" height="28" viewBox="0 0 26 28"><circle cx="13" cy="8" r="7" fill="#fff"/><path d="M0 28c0-8 5-12 13-12s13 4 13 12z" fill="#fff"/></svg>MY PROFILE</div>
</aside>

<h1 class="page-title">EVENTS</h1>
<div class="event-tabs"><div class="current"></div><div></div><div></div><div></div><div></div></div>
<div class="event-card"></div>
<div class="event-photo" role="img" aria-label="Photo of a runner crossing the finish line"></div>
<p class="event-text">taciti sociosqu ad litora torquent per conubia<br>nostra per inceptos hymenaeos</p>

<div class="shade"></div>

<section class="promo">
  <div class="promo-inner">
    <h2 class="promo-title">Sociosqu ad litora torquent per conubia<br>nostra per inceptos hymenaeos</h2>
    <p class="promo-text">Praesent elementum elit at tellus Curabitur metus ipsum<br>luctus eu malesuada ut tincidunt sed</p>
    <a href="#" class="promo-button">CLICK HERE</a>
  </div>
</section>

<footer class="site-footer">© 2016 Company Name&nbsp; All right reserved&nbsp; Term of Use</footer>
</body>
</html>
```